Yacht, Boats, Watersports company needs a redesign of business card

Hello Designers!
We are a Boat dealership company that sells fun in the water, we sell boats, Yachts, Kayaks and also yacht WaterSport toys. We are looking to redesign our business cards in to something a little bit more sophisticated. in a way that we can make better use of our company colors. I'm attaching a zipped file containing the company 3 sets of company logo which one is an horizontal another one is a vertical and also a chromed 3d logo. Also is included two set of business cards that we use and also some designs that i think it's interesting. We use PMS 2026c Orange and PMS 7687C Blue. I would like to see at least two different options with the orange as accent and also using blue as an accent color. It's really important for the business cards to have a font option and size that is legible to most people. Our current website is wwww.coralpennant.com. Please visit if you want to have a better feeling of the Boat dealership
You can send Single sided or double side options. We are now using single sided but we may be open for a double side option if we really like the design.
Target Market(s)
Marine, boat sales, yacht sales, water toys sales/
Contact Information for Business Card
Name: Dale Whitcombe
Address: 212 North Fenwick Lane,
Harbor Point, FL 33990
Phone: 555-731-8842
Fax: 555:731-8843
Cell: 555-382-1490
Email: dw@coralpennant.com
Website: coralpennant.com
Requirements
Must have
- the current information of the business card provided.
logo
use the PMS Colors
Nice to have
- a touch of elegance and sophistication but simple
Should not have
- should not have any typography that is hard to read, the card should be simple but yet sophisticated.

```html
<!DOCTYPE html>
<html lang="en">
<head>
<meta charset="utf-8">
<title>Coral Pennant Business Cards</title>
<link rel="stylesheet" href="https://fonts.googleapis.com/css2?family=Arimo:wght@400;700&family=Montserrat:wght@700&display=swap">
<style>
  :root {
    --blue: #1b55a0;
    --orange: #f26d21;
    --bleed: #b5b5b5;
    --white: #ffffff;
    --label: #222222;
  }
  * { box-sizing: border-box; margin: 0; padding: 0; }
  html, body { width: 1200px; height: 1200px; overflow: hidden; background: var(--white); }
  .sheet { position: relative; width: 1200px; height: 1200px; font-family: "Arimo", Arial, sans-serif; }

  .bleed-area { position: absolute; width: 563px; height: 338px; background: var(--bleed); }
  .bleed-area--tl { left: 21px; top: 235px; }
  .bleed-area--tr { left: 608px; top: 235px; }
  .bleed-area--bl { left: 21px; top: 614px; }
  .bleed-area--br { left: 608px; top: 614px; }

  .bleed-label { position: absolute; font-size: 11px; color: var(--label); }
  .bleed-label--bottom { bottom: -1px; left: 50%; transform: translateX(-50%); }
  .bleed-label--side { left: 2px; top: 50%; transform: translateY(-50%) rotate(90deg); transform-origin: center; }

  .card { position: absolute; left: 17px; top: 17px; width: 529px; height: 306px; border-radius: 40px; overflow: hidden; }
  .card--white { background: var(--white); }
  .card--orange { background: var(--orange); }
  .card--blue { background: var(--blue); }

  .card__band { position: absolute; left: 0; right: 0; bottom: 0; height: 48px; display: flex; align-items: center; justify-content: center; color: var(--white); font-size: 15px; letter-spacing: 2.5px; }
  .card__band--blue { background: var(--blue); }
  .card__band--orange { background: var(--orange); }

  .brand { position: absolute; left: 0; right: 0; top: 50px; display: flex; flex-direction: column; align-items: center; }
  .brand__mark { width: 96px; height: 96px; border-radius: 50%; border: 9px solid var(--orange); }
  .brand__name { margin-top: 22px; font-family: "Montserrat", Arial, sans-serif; font-weight: 700; font-size: 27px; letter-spacing: 1px; color: var(--blue); }

  .person { position: absolute; left: 27px; top: 25px; }
  .person__name { font-weight: 700; font-size: 22px; text-transform: uppercase; }
  .person__title { margin-top: 4px; font-weight: 700; font-size: 13px; color: var(--white); text-transform: uppercase; letter-spacing: .3px; }
  .card--orange .person__name { color: var(--blue); }
  .card--blue .person__name { color: var(--orange); }

  .contacts { position: absolute; left: 250px; top: 70px; list-style: none; }
  .contacts__row { display: flex; align-items: center; height: 40px; }
  .contacts__icon { width: 24px; height: 24px; flex: none; margin-right: 12px; }
  .contacts__text { font-size: 14px; line-height: 15px; }
  .card--orange .contacts__text { color: var(--blue); }
  .card--blue .contacts__text { color: var(--orange); }

  .social { position: absolute; left: 27px; top: 193px; display: flex; gap: 6px; }
  .social__tile { width: 22px; height: 22px; background: var(--blue); }
  .card--blue .social__tile { background: var(--orange); }

  .swatches { position: absolute; left: 1010px; top: 1158px; display: flex; }
  .swatch { width: 63px; height: 42px; }
  .swatch--blue { background: var(--blue); }
  .swatch--orange { background: var(--orange); }
</style>
</head>
<body>
<main class="sheet">

  <svg width="0" height="0" style="position:absolute">
    <defs>
      <symbol id="icon-phone" viewBox="0 0 24 24"><circle cx="12" cy="12" r="12" fill="#fff"/><path d="M6 10c0-2 3-3 6-3s6 1 6 3l-2 1-1-2h-6l-1 2zM8 12h8l1 5H7z" fill="currentColor"/></symbol>
      <symbol id="icon-fax" viewBox="0 0 24 24"><circle cx="12" cy="12" r="12" fill="#fff"/><path d="M8 6h8v4H8zM5 10h14v7H5zM8 14h8v4H8z" fill="currentColor"/></symbol>
      <symbol id="icon-home" viewBox="0 0 24 24"><circle cx="12" cy="12" r="12" fill="#fff"/><path d="M12 5l7 6h-2v7h-4v-4h-2v4H7v-7H5z" fill="currentColor"/></symbol>
      <symbol id="icon-mail" viewBox="0 0 24 24"><circle cx="12" cy="12" r="12" fill="#fff"/><path d="M6 8h12v9H6z" fill="currentColor"/><path d="M6 8l6 5 6-5" fill="none" stroke="#fff" stroke-width="1.4"/></symbol>
    </defs>
  </svg>

  <section class="bleed-area bleed-area--tl">
    <div class="card card--white">
      <div class="brand"><div class="brand__mark"></div><div class="brand__name">CORAL PENNANT</div></div>
      <div class="card__band card__band--blue">www.coralpennant.com</div>
    </div>
    <span class="bleed-label bleed-label--side">bleed</span>
    <span class="bleed-label bleed-label--bottom">bleed</span>
  </section>

  <section class="bleed-area bleed-area--tr">
    <div class="card card--white">
      <div class="brand"><div class="brand__mark"></div><div class="brand__name">CORAL PENNANT</div></div>
      <div class="card__band card__band--orange">www.coralpennant.com</div>
    </div>
    <span class="bleed-label bleed-label--side">bleed</span>
    <span class="bleed-label bleed-label--bottom">bleed</span>
  </section>

  <section class="bleed-area bleed-area--bl">
    <div class="card card--orange">
      <div class="person"><div class="person__name">Dale Whitcombe</div><div class="person__title">Corporate Manager</div></div>
      <ul class="contacts" style="color:var(--orange)">
        <li class="contacts__row"><svg class="contacts__icon"><use href="#icon-phone"/></svg><span class="contacts__text">1.555.731.8842<br>1.555.382.1490</span></li>
        <li class="contacts__row"><svg class="contacts__icon"><use href="#icon-fax"/></svg><span class="contacts__text">1.555.731.8843</span></li>
        <li class="contacts__row"><svg class="contacts__icon"><use href="#icon-home"/></svg><span class="contacts__text">212 North Fenwick Lane<br>Harbor Point, FL 33990</span></li>
        <li class="contacts__row"><svg class="contacts__icon"><use href="#icon-mail"/></svg><span class="contacts__text">dw@coralpennant.com</span></li>
      </ul>
      <div class="social"><span class="social__tile"></span><span class="social__tile"></span><span class="social__tile"></span></div>
      <div class="card__band card__band--blue">www.coralpennant.com</div>
    </div>
    <span class="bleed-label bleed-label--side">bleed</span>
    <span class="bleed-label bleed-label--bottom">bleed</span>
  </section>

  <section class="bleed-area bleed-area--br">
    <div class="card card--blue">
      <div class="person"><div class="person__name">Dale Whitcombe</div><div class="person__title">Corporate Manager</div></div>
      <ul class="contacts" style="color:var(--blue)">
        <li class="contacts__row"><svg class="contacts__icon"><use href="#icon-phone"/></svg><span class="contacts__text">1.555.731.8842<br>1.555.382.1490</span></li>
        <li class="contacts__row"><svg class="contacts__icon"><use href="#icon-fax"/></svg><span class="contacts__text">1.555.731.8843</span></li>
        <li class="contacts__row"><svg class="contacts__icon"><use href="#icon-home"/></svg><span class="contacts__text">212 North Fenwick Lane<br>Harbor Point, FL 33990</span></li>
        <li class="contacts__row"><svg class="contacts__icon"><use href="#icon-mail"/></svg><span class="contacts__text">dw@coralpennant.com</span></li>
      </ul>
      <div class="social"><span class="social__tile"></span><span class="social__tile"></span><span class="social__tile"></span></div>
      <div class="card__band card__band--orange">www.coralpennant.com</div>
    </div>
    <span class="bleed-label bleed-label--side">bleed</span>
    <span class="bleed-label bleed-label--bottom">bleed</span>
  </section>

  <div class="swatches"><span class="swatch swatch--blue"></span><span class="swatch swatch--orange"></span></div>
</main>
</body>
</html>
```